New Business Cards for Tormin Group

We need a new Business Card to compliment our new logo. We are a vibrant design, manufacture and install business providing recreation areas, public parks and Municipal spaces. We want business cards that are classy, modern and clean.

We have recently changed our logo, and are celebrating our 40th anniversary. We want business cards with a new modern design to reflect our status.

Target Market(s)

Customers

Contact Information for Business Card

We need all the details of our 3 offices as per the business card attached. Please disregard the old logo on the business card, the other three files show our new logo.

Requirements
Must have
• All info as per attached business card but with new logo.
Nice to have

```html
<!DOCTYPE html>
<html lang="en">
<head>
<meta charset="utf-8">
<title>Tormin Group – Business Card</title>
<link href="https://fonts.googleapis.com/css2?family=Lato:wght@400;700&display=swap" rel="stylesheet">
<style>
  :root {
    --backdrop: #5e5e5e;
    --card: #ffffff;
    --brand-red: #e8303a;
    --ink-dark: #3d3d3f;
    --ink-body: #5a5a5c;
    --ink-muted: #727274;
    --rule-grey: #d6d6d6;
    --band-dark: #47474a;
    --faint-mark: #f4f4f4;
  }
  html, body {
    margin: 0;
    width: 1200px;
    height: 1200px;
    overflow: hidden;
    background: var(--backdrop);
    font-family: "Lato", sans-serif;
  }
  .business-card {
    position: absolute;
    left: 70px;
    top: 292px;
    width: 1059px;
    height: 615px;
    background: var(--card);
    overflow: hidden;
  }
  .faint-mark {
    position: absolute;
    left: 220px;
    top: -20px;
    width: 520px;
    height: 520px;
    border-radius: 50%;
    background: var(--faint-mark);
    opacity: 0.7;
  }
  .abs { position: absolute; margin: 0; white-space: nowrap; }
  .person-name {
    left: 43px; top: 98px;
    font-size: 37px; font-weight: 400; color: var(--brand-red);
  }
  .person-name .first { font-weight: 700; }
  .person-title {
    left: 43px; top: 155px;
    font-size: 24px; color: var(--ink-dark);
  }
  .direct-contact {
    left: 43px; font-size: 19.5px; color: var(--ink-dark);
  }
  .direct-contact .label { color: var(--brand-red); }
  .direct-phone { top: 255px; }
  .direct-email { top: 296px; }
  .divider-grey {
    left: 43px; top: 345px; width: 978px; height: 2px; background: var(--rule-grey);
  }
  .divider-red {
    left: 43px; top: 344px; width: 314px; height: 4px; background: var(--brand-red);
  }
  .office { position: absolute; top: 364px; }
  .office-name {
    margin: 0 0 10px; font-size: 25px; font-weight: 400; color: var(--brand-red);
  }
  .office-line {
    margin: 0; font-size: 19.5px; line-height: 31.5px; color: var(--ink-muted);
  }
  .office-head { left: 43px; }
  .office-dubai { left: 414px; }
  .office-qatar { left: 753px; top: 368px; }
  .brand-lockup {
    position: absolute; left: 740px; top: 92px;
    display: flex; align-items: center; gap: 16px;
  }
  .brand-dot {
    width: 64px; height: 64px; border-radius: 50%; background: var(--brand-red);
  }
  .brand-name {
    font-size: 40px; font-weight: 700; color: var(--ink-dark); letter-spacing: 0.5px;
  }
  .footer-band { position: absolute; left: 0; bottom: 0; }
  .website {
    right: 35px; top: 578px;
    font-size: 20px; font-weight: 700; color: #ffffff;
  }
</style>
</head>
<body>
  <div class="business-card">
    <div class="faint-mark" aria-hidden="true"></div>

    <h1 class="abs person-name"><span class="first">Sami</span> Haddara</h1>
    <p class="abs person-title">Managing Partner</p>

    <p class="abs direct-contact direct-phone"><span class="label">Phone:</span> +971 (0)50 384 7726</p>
    <p class="abs direct-contact direct-email"><span class="label">Email:</span> sami@tormingroup.com</p>

    <div class="abs divider-grey"></div>
    <div class="abs divider-red"></div>

    <div class="brand-lockup">
      <span class="brand-dot" aria-hidden="true"></span>
      <span class="brand-name">TORMIN GROUP</span>
    </div>

    <section class="office office-head">
      <h2 class="office-name">Head Office</h2>
      <p class="office-line">P.O. Box: 31842 Abu Dhabi. U.A.E</p>
      <p class="office-line">Tel No: +971 (0)2 4471930</p>
      <p class="office-line">Fax No: +971(0)2 4471931</p>
      <p class="office-line">Email: sales@tormingroup.com</p>
    </section>

    <section class="office office-dubai">
      <h2 class="office-name">Dubai Office</h2>
      <p class="office-line">P.O. Box: 417265 Dubai, U.A.E</p>
      <p class="office-line">Tel No: +971 (0)4 462718</p>
      <p class="office-line">Fax No: +971(0)4 462805</p>
      <p class="office-line">Email: sales@tormingroup.com</p>
    </section>

    <section class="office office-qatar">
      <h2 class="office-name">Qater Office</h2>
      <p class="office-line">P.O. Box: 17390 Doha, Qatter</p>
      <p class="office-line">Tel No: +974 44518362</p>
      <p class="office-line">Fax No: +971 44527614</p>
      <p class="office-line">Email: sales@tormingroup.com</p>
    </section>

    <svg class="footer-band" width="1059" height="62" viewBox="0 0 1059 62" aria-hidden="true">
      <path d="M0 16 H520 Q530 16 538 12 L548 7 Q556 3 566 3 H1059 V62 H0 Z" fill="var(--band-dark)"/>
      <path d="M0 12 H528 L510 25 H0 Z" fill="var(--brand-red)"/>
      <rect x="0" y="25" width="540" height="4" fill="#ffffff"/>
    </svg>

    <p class="abs website">www.tormingroup.com</p>
  </div>
</body>
</html>
```